Home Health Company Needs a Corporate Identity Package

We need a corporate identity package (see what it should include below) for a home health care company. The design should be professional, uncluttered, simple and created in Publisher (so that we can edit the design in the future, if necessary. )
We need the following created:
-Presentation folder
-Business card template (color, double sided)
-Letterhead
-Stationary
-postcard sized marketing piece (5.5" x 8.5", color, double sided)

Target Market(s)

We are in the business of supplying personal care aids for in home care. Our services are directed towards older, retired individuals with some disability or illness. However, we will be marketing to the children or relatives of our in home clients. We want our logo to emphasize our reliability and personalized services.

Industry/Entity Type

Home Health Care

Requirements
Must have
• The design should be professional, uncluttered, simple and created in Publisher (so that we can edit the design in the future, if necessary. )

```html
<!DOCTYPE html>
<html lang="en">
<head>
<meta charset="utf-8">
<title>Willowbrook Home Care – Envelope</title>
<link href="https://fonts.googleapis.com/css2?family=Open+Sans:wght@400;700&display=swap" rel="stylesheet">
<style>
  :root {
    --sky: #4cc7f0;
    --slate: #5a5b5e;
    --paper: #ffffff;
    --backdrop: #e9eaec;
    --edge: #d5d7da;
  }
  * { box-sizing: border-box; margin: 0; padding: 0; }
  html, body { width: 1200px; height: 892px; overflow: hidden; }
  body {
    background: var(--backdrop);
    font-family: "Open Sans", Arial, sans-serif;
    position: relative;
  }
  .envelope {
    position: absolute;
    width: 760px;
    height: 380px;
    background: var(--paper);
    border: 1px solid var(--edge);
    overflow: hidden;
  }
  .envelope--front { left: 220px; top: 46px; }
  .envelope--back { left: 220px; top: 466px; }

  /* Front */
  .brand {
    position: absolute;
    left: 40px;
    top: 36px;
    display: flex;
    align-items: center;
    gap: 14px;
  }
  .brand__dot {
    width: 42px;
    height: 42px;
    border-radius: 50%;
    background: var(--sky);
  }
  .brand__name {
    font-weight: 700;
    font-size: 34px;
    line-height: 1.05;
    color: var(--slate);
    letter-spacing: -0.5px;
  }
  .footer-rule {
    position: absolute;
    left: 0; right: 0;
    bottom: 74px;
    height: 6px;
    background: var(--slate);
  }
  .footer-band {
    position: absolute;
    left: 0; right: 0;
    bottom: 0;
    height: 74px;
    background: var(--sky);
  }
  .footer-band__address {
    position: absolute;
    left: 28px;
    top: 12px;
    font-size: 12px;
    color: var(--paper);
  }
  .corner-mark {
    position: absolute;
    right: -30px;
    bottom: -30px;
    width: 110px;
    height: 110px;
    border-radius: 50%;
    background: rgba(255,255,255,0.55);
  }

  /* Back */
  .flap {
    position: absolute;
    left: 0; right: 0; top: 0;
    height: 92px;
    background: var(--sky);
    border-bottom-right-radius: 46px;
  }
  .flap__mark {
    position: absolute;
    left: 400px;
    top: 92px;
    width: 56px;
    height: 56px;
    border-radius: 50%;
    background: var(--sky);
  }
</style>
</head>
<body>

  <section class="envelope envelope--front" aria-label="Envelope front">
    <div class="brand">
      <span class="brand__dot"></span>
      <span class="brand__name">Willowbrook<br>Home Care</span>
    </div>
    <div class="footer-rule"></div>
    <div class="footer-band">
      <p class="footer-band__address">Suite 12-Second Floor, Maple Court, Riverside-48210, Lakeview, Canada</p>
      <span class="corner-mark"></span>
    </div>
  </section>

  <section class="envelope envelope--back" aria-label="Envelope back">
    <div class="flap"></div>
    <span class="flap__mark"></span>
  </section>

</body>
</html>
```